Vensol Holdings Web Design

Vensol Holdings Limited Shenzhen

This project is a 10 page launch website.
Our client is seeking a contemporary homepage design for a Holdings company. Once we are happy with the homepage design and select designer we will request a secondary page design.

Please see attached company LOGO for an idea of style, it incorporates the traditional Chinese furniture lattice work. The Corvel crest website is one of our clients favorite so we would like to see a similar homepage design to this website.

Use the websites below for reference purpose. The first two are Chinese and the second two are international. We would like to see elements of both but more focus on international design.

http://www.evergrande.com/http://www.taurenfield.com/pub/default.aspx http://www.corvelcrest.com/zh/maldives_lorinhaven/
http://www.quelba-studio.com
http://media-cache-ex0.snapvalu.com/originals/71/a3/19/71a319c5b2d04e8f6a17c3b9e5d0f4a1.jpg

Company Background
VENSOL HOLDINGS, located in Qianhai, China, is a new real-estate project operator, structuring urban-rural real-estate investment and development, and industrial fund investment. The company also invests in supply chain management and supporting infrastructures. To create new spaces and livable cities Vensol Holdings develop win-win strategic partnerships with a number of institutions. Currently cooperating with Tianjing North Lumore, China urban and rural integrated demonstration.

Target Market(s)

B2B property investment. Target market customers are senior level management/decision makers of large corporations. Focusing geographically on the domestic market first and expanding internationally in 2nd and 3rd years.

Industry/Entity Type

Investment

Requirements
Must have
• Since this is a new company, we would like to the website representing growth and power, E.g. like a growing tree.
Should not have
• Low-level vectors such as curency symbols, American dollar.

```html
<!DOCTYPE html>
<html lang="en">
<head>
<meta charset="utf-8">
<title>Vensol Holdings</title>
<link rel="stylesheet" href="https://fonts.googleapis.com/css2?family=Ubuntu:ital,wght@0,400;0,500;0,700;1,400&family=Roboto+Condensed:wght@400;700&family=Questrial&family=Arimo:wght@400;700&display=swap">
<style>
:root{
  --gold:#c8962a;
  --gold-soft:#d9a740;
  --orange:#f0a020;
  --orange-dark:#d88a10;
  --ink:#2b2b2b;
  --text:#6a6a6a;
  --muted:#9a9a9a;
  --paper:#f3f3f3;
  --line:#d8d8d8;
  --night:#1d1e20;
  --footer:#2a2a2a;
  --footer-deep:#1a1a1a;
  --white:#ffffff;
  --link:#2a5ea8;
}
*{margin:0;padding:0;box-sizing:border-box}
html,body{width:678px;height:1200px;overflow:hidden;background:var(--paper)}
body{position:relative;font-family:"Ubuntu",sans-serif;color:var(--text)}
h1,h2,h3,h4{font-weight:400}
.abs{position:absolute}

/* header */
.site-header{left:0;top:0;width:678px;height:61px;background:linear-gradient(#fafafa,#ececec)}
.brand{left:85px;top:5px;width:60px;text-align:center}
.brand-mark{width:34px;height:34px;margin:0 auto;border-radius:50%;background:var(--gold)}
.brand-name{margin-top:4px;font-family:"Ubuntu",sans-serif;font-size:8px;color:var(--gold);white-space:nowrap;margin-left:-6px}
.search{left:413px;top:3px;width:135px;height:20px;background:var(--white);border:1px solid var(--line);font-size:8px;color:#777;padding:5px 6px}
.search svg{position:absolute;right:5px;top:4px}
.lang{left:551px;top:3px;width:37px;height:20px;background:var(--white);border:1px solid var(--line)}
.lang .flag{position:absolute;left:6px;top:6px;width:10px;height:7px;background:#c8d0e0}
.lang .caret{position:absolute;right:6px;top:8px;border:4px solid transparent;border-top-color:#444}
.nav{left:303px;top:34px;display:flex;align-items:center;font-family:"Arimo",sans-serif;font-weight:700;font-size:10px;color:var(--ink)}
.nav a{text-decoration:none;color:inherit}
.nav .active{display:inline-block;width:50px;height:21px;line-height:21px;text-align:center;background:linear-gradient(var(--orange),var(--orange-dark));border-radius:3px;color:var(--white);margin-right:17px}
.nav .item{margin-right:21px}

/* hero */
.hero{left:0;top:61px;width:678px;height:354px;background:radial-gradient(ellipse at 70% 20%,#8a6a3a 0%,#4a3a2c 35%,#1e1a18 75%)}
.hero-title{left:0;top:327px;width:678px;text-align:center;font-family:"Questrial",sans-serif;font-size:40px;color:var(--white);letter-spacing:0.5px}
.hero-sub{left:0;top:372px;width:678px;text-align:center;font-family:"Questrial",sans-serif;font-size:18px;color:var(--white)}
.dots{display:flex;gap:3px}
.dots i{width:5px;height:5px;border-radius:50%;background:var(--white);display:block}
.dots i.on{background:var(--gold)}
.dots.hollow i{background:transparent;border:1px solid #bbb}
.dots.hollow i.on{background:var(--gold);border-color:var(--gold)}

/* intro */
.intro{left:0;top:415px;width:678px;height:179px;background:var(--paper)}
.section-title{font-family:"Roboto Condensed",sans-serif;color:var(--gold);font-size:18px;font-weight:400}
.body-copy{font-size:7.6px;line-height:12px;color:var(--text)}
.news{left:448px;top:445px;width:145px;height:115px;background:var(--white);border:1px solid #e2e2e2;box-shadow:0 1px 3px rgba(0,0,0,.12)}
.tabs{display:flex;font-size:7.5px;height:14px;border-bottom:1px solid #ddd}
.tabs span{padding:3px 6px;line-height:8px}
.tabs .on{color:var(--link);border:1px solid #ddd;border-bottom:none;background:var(--white)}
.tabs .off{background:#e4e4e4;color:#888;margin-left:2px}
.tweet{padding:0 10px;margin-top:8px;font-size:6px;line-height:8px;font-style:italic;color:#777}
.tweet b{font-weight:400;color:var(--gold)}
.tweet em{display:block;color:#aaa}

/* features */
.features{left:0;top:594px;width:678px;height:277px;background:linear-gradient(100deg,#26282b 0%,#1a1b1d 45%,#222426 100%)}
.feature-rule{left:85px;top:675px;width:35px;height:2px;background:var(--gold)}
.feature-name{left:85px;top:689px;font-size:10px;font-weight:700;color:var(--white)}
.feature-copy{left:85px;top:706px;width:145px;font-size:8px;line-height:12px;color:#e4e4e4}
.feature-photo{left:246px;top:651px;width:346px;height:164px;background:linear-gradient(#7aa0bf 0%,#9bb4c4 35%,#c9c2b2 50%,#5f7e3e 75%,#3f5a2a 100%);box-shadow:0 2px 6px rgba(0,0,0,.5)}

/* testimonial */
.testimonial{left:0;top:871px;width:678px;height:186px;background:var(--paper)}
.quote-mark{left:88px;top:900px;font-family:Georgia,serif;font-size:44px;line-height:44px;color:#c9c9c9}
.quote{left:122px;top:906px;width:470px;font-size:7.6px;line-height:12.6px;font-style:italic;color:#666}
.author-photo{left:123px;top:975px;width:47px;height:47px;border-radius:50%;border:3px solid var(--white);box-shadow:0 0 0 1px #ccc;background:linear-gradient(#cfd6de,#7b8594)}
.author-name{left:185px;top:984px;font-family:"Roboto Condensed",sans-serif;font-size:10px;color:var(--gold)}
.author-role{left:185px;top:998px;font-size:7px;color:#666}

/* footer */
.footer{left:0;top:1057px;width:678px;height:118px;background:linear-gradient(#2f2f2f,#242424)}
.footer-title{font-family:"Roboto Condensed",sans-serif;font-size:12px;font-weight:400;color:var(--gold-soft)}
.footer-list{list-style:none;font-size:7px;line-height:11.7px;color:#cfcfcf}
.footer-list li::before{content:"";display:inline-block;width:3px;height:3px;border-radius:50%;background:#cfcfcf;margin:0 7px 1px 1px;vertical-align:middle}
.divider{top:1064px;width:1px;height:96px;background:#444}
.signup{left:341px;top:1130px;width:250px;height:29px;background:#1c1c1c;border-radius:3px}
.signup-input{left:347px;top:1135px;width:188px;height:19px;background:var(--white);font-size:7px;color:#666;padding:6px 6px}
.signup-btn{left:540px;top:1135px;width:45px;height:19px;background:var(--orange);color:#4a2a00;font-size:6.5px;text-align:center;line-height:19px}
.legal{left:0;top:1175px;width:678px;height:25px;background:var(--footer-deep)}
.legal-text{left:85px;top:1184px;font-size:6.5px;color:#bbb}
.social{top:1179px;width:17px;height:17px;border-radius:50%}
</style>
</head>
<body>

<header class="abs site-header"></header>
<div class="abs brand">
  <div class="brand-mark"></div>
  <div class="brand-name">Vensol Holdings</div>
</div>
<div class="abs search">Search
  <svg width="10" height="10" viewBox="0 0 10 10"><circle cx="4" cy="4" r="3" fill="none" stroke="#333" stroke-width="1.3"/><line x1="6.2" y1="6.2" x2="9" y2="9" stroke="#333" stroke-width="1.4"/></svg>
</div>
<div class="abs lang"><span class="flag"></span><span class="caret"></span></div>
<nav class="abs nav">
  <a class="active" href="#">HOME</a>
  <a class="item" href="#">ABOUT</a>
  <a class="item" href="#">SERVICES</a>
  <a class="item" href="#">BLOG</a>
  <a href="#">CONTACT</a>
</nav>

<section class="abs hero" role="img" aria-label="Three smiling business people in suits in front of city lights at night"></section>
<h1 class="abs hero-title">Morbi tristique senectus</h1>
<p class="abs hero-sub">Pellentesque habitant morbi tristique netus et malesuada</p>
<div class="abs dots" style="left:327px;top:402px"><i class="on"></i><i></i><i></i><i></i></div>

<section class="abs intro"></section>
<h2 class="abs section-title" style="left:85px;top:441px">Varius turpis ut neque eleifend scelerisque</h2>
<p class="abs body-copy" style="left:85px;top:470px;width:328px">Consectetur adipiscing elit. Etiam felis ante, laoreet vel mi commodo, dapibus porta lectus. Sed elementum scelerisque nunc, non accumsan est pretium nec. Nunc ac lacinia diam, in ultrices orci. Lorem ipsum dolor sit amet, consectetur adipiscing elit. Pellentesque habitant morbi tristique senectus et netus et malesuada fames ac turpis egestas. Pellentesque habitant morbi tristique senectus et netus et malesuada fames ac turpis egestas.</p>
<p class="abs body-copy" style="left:85px;top:540px;width:328px">Consectetur adipiscing elit. Etiam felis ante, laoreet vel mi commodo, dapibus porta lectus. Sed elementum scelerisque nunc, non accumsan est pretium nec.</p>
<aside class="abs news">
  <div class="tabs"><span class="on">News</span><span class="off">Reviews &amp; Awards</span></div>
  <div class="tweet"><b>@MarcoDelling on Chirper</b><em>02 Jun 2014</em>Lorem ipsum dolor sit amet, consectetur adipiscing elit. Etiam felis ante....</div>
  <div class="tweet"><b>@MarcoDelling on Chirper</b><em>02 Jun 2014</em>Lorem ipsum dolor sit amet, consectetur adipiscing elit. Etiam felis ante....</div>
</aside>
<div class="abs dots hollow" style="left:449px;top:566px"><i class="on"></i><i></i><i></i><i></i></div>

<section class="abs features" role="img" aria-label="Dark background of office towers at night"></section>
<h2 class="abs section-title" style="left:85px;top:649px">Feature Projects</h2>
<div class="abs feature-rule"></div>
<h3 class="abs feature-name">Lectus Scelerisque</h3>
<div class="abs feature-copy">
  <p>Consectetur adipiscing elit. Etiam felis ante, laoreet vel mi commodo, dapibus porta lectus scelerisque.</p>
  <p style="margin-top:8px">Consectetur adipiscing elit. Etiam felis ante, laoreet vel mi commodo, dapibus porta lectus scelerisqu nunc accumsan est pretium nec.</p>
</div>
<div class="abs dots" style="left:85px;top:807px"><i class="on"></i><i></i><i></i><i></i></div>
<div class="abs feature-photo" role="img" aria-label="White villa with red roof among trees by the sea"></div>

<section class="abs testimonial"></section>
<div class="abs quote-mark">&ldquo;</div>
<p class="abs quote">Pellentesque habitant morbi tristique senectus et netus et mesuada fames ac turpis egestas. Pellenue habitant morbi tristique senectus et netus et malesuada fames ac turpis egestas Quisque urna mi, faucibus at magna vel, venenatis ornare sem&nbsp; Pellentesque habitant morbi tristique senectus et netus et malesuada fames ac turpis egestas.</p>
<svg class="abs" style="left:122px;top:950px" width="471" height="12" viewBox="0 0 471 12"><path d="M0 4.5H18L23 10L28 4.5H471" fill="none" stroke="#c8c8c8" stroke-width="1"/></svg>
<div class="abs author-photo" role="img" aria-label="Portrait of the quoted client"></div>
<div class="abs author-name">Consectetur Adipiscing</div>
<div class="abs author-role">Lorem ipsum</div>
<div class="abs dots hollow" style="left:566px;top:1003px"><i class="on"></i><i></i><i></i><i></i></div>

<footer class="abs footer"></footer>
<h4 class="abs footer-title" style="left:85px;top:1071px">Our Services</h4>
<ul class="abs footer-list" style="left:85px;top:1096px">
  <li>Consectetur adipiscing</li><li>Etiam felis ante laoreet</li><li>Commodo dapibus porta</li><li>Lectus Sed elementum</li><li>Scelerisque accumsan</li>
</ul>
<div class="abs divider" style="left:188px"></div>
<h4 class="abs footer-title" style="left:205px;top:1071px">Condimentum est</h4>
<ul class="abs footer-list" style="left:205px;top:1096px">
  <li>Pellentesque habitant morbi</li><li>tristique senectus et netus et</li><li>malesuada fames ac turpis</li><li>egestas. Pellentesque</li><li>habitant morbi tristique</li>
</ul>
<div class="abs divider" style="left:320px"></div>
<h4 class="abs footer-title" style="left:341px;top:1071px">Subscribe our newsletter</h4>
<p class="abs footer-list" style="left:341px;top:1098px;width:255px;line-height:12px">Habitant morbi tristique senectus et netus et malesuada fames<br>ac turpis egestas. Quisque urna mi, faucibus at magna vel, venenatis ornare sem.</p>
<div class="abs signup"></div>
<div class="abs signup-input">Enter your email here</div>
<div class="abs signup-btn">SUBSCRIBE</div>

<div class="abs legal"></div>
<div class="abs legal-text">Vensol Holdings &copy; All rights reserved.</div>
<span class="abs social" style="left:535px;background:#3b5a9a"></span>
<span class="abs social" style="left:555px;background:#2aa3e0"></span>
<span class="abs social" style="left:575px;background:#d9402e"></span>

</body>
</html>
```